Flyer-Design für Tauchunternehmen im südlichen Ägypten
Zielgruppe
Wir sind ein Tauchunternehmen im südlichen Ägypten, mit dem Hauptaugenmerk auf unser Tauchcenter und Meroka.
Aufgabenstellung
Es ist mir bewusst, dass es viel Content ist. Dieser kann ggf. auch angepasst werden. Der Flyer sollte in einem gängigen Format gedruckt werden können. Lieber mehrseitig, all flächenmässig zu gross.
Die beiden erwähnten Boote gehören unbedingt zu Meroka.
Die Zip Dateien sind auf die Themen abgestimmt, resp. das allgemeine Diving kann beliebig eingesetzt werden. Je ein Exemplar in Deutsch und Englisch wäre super. Beide Texte liegen vor.
Velora Diving Safari - Entdecke das Rote Meer
Wir zeigen euch unser tolles, vielfältiges zu Hause mit den schönsten Tauchplätzen.
Ob ihr erfahrene Taucher seid oder gerade erst euer Tauchabenteuer begonnen habt, erlebt mit uns die Schönheit der Unterwasserwelt mit ihren vielfältigen Korallen und Fischen.
Entfliehe mit uns dem Alltag.
Wir freuen uns, dich bei uns begrüssen zu dürfen!
Team Velora Diving Safari
Tarek & Petra
…..and into the ocean we go, to lose our mind and find our soul
Velora Diving Safari - Discover the Red Sea
We show you our great, diverse home with the most beautiful dive sites.
Whether you are an experienced diver or just starting your diving adventure, discover with us the beauty of the underwater world with its varied corals and fish.
Escape the daily routine with us.
We look forward to welcoming you!
.....and into the ocean we go, to lose our mind and find our soul
Tauchcenter
Wir sind im Hotel Belvano, südlich von El Quseir zu Hause. Von hier aus starten wir täglich zum Tauchen und Schnorcheln am Hausriff, vom Strand an die umliegenden Riffe und unseren Tagesbooten ab Port Ghalib und Hamata. Unser Team begleitet dich professionell bei deinen ersten Atemzügen unter Wasser, bildet dich nach QRX und BEMO-Standard aus oder führt dich sicher entlang der Tauchplätze.
Wir offerieren attraktive Arrangements mit Hotel und Tauchen..

```html
<!DOCTYPE html>
<html lang="en">
<head>
<meta charset="utf-8">
<title>Velora Diving Safari – Tri-fold Flyer</title>
<link href="https://fonts.googleapis.com/css2?family=Poppins:ital,wght@0,400;0,600;0,700;1,400&display=swap" rel="stylesheet">
<style>
  :root{
    --navy:#0b3460;
    --navy-deep:#082a4f;
    --sea:#1e9be0;
    --sea-light:#7fd0f5;
    --sea-pale:#cdeefc;
    --ink:#1d2b3a;
    --paper:#ffffff;
    --stage:#d6d6d6;
    --accent-red:#d8261f;
  }
  *{box-sizing:border-box;margin:0;padding:0}
  html,body{width:1148px;height:1200px;overflow:hidden;background:var(--stage);font-family:"Poppins",sans-serif;color:var(--ink)}
  .spread{position:absolute;left:174px;width:800px;height:570px;background:var(--paper);overflow:hidden;box-shadow:0 4px 14px rgba(0,0,0,.12)}
  .spread--inside{top:20px}
  .spread--outside{top:610px}
  .abs{position:absolute}
  .wave{position:absolute;pointer-events:none}
  h3{font-size:10.5px;font-weight:700;color:var(--navy);line-height:1.2;margin-bottom:6px}
  p{font-size:6.6px;line-height:1.62}
  .block{position:absolute}
  .photo{position:absolute}
  .navy{background:var(--navy)}
  .on-navy,.on-navy h3,.on-navy p{color:#fff}
  .headline-bar{position:absolute;left:270px;top:14px;width:530px;height:36px;background:var(--navy);color:#fff;font-weight:600;font-size:10.5px;display:flex;align-items:center;padding-left:22px}
  .brand{position:absolute;display:flex;flex-direction:column;align-items:center}
  .brand__mark{width:74px;height:74px;border-radius:50%;border:2px solid var(--navy)}
  .brand__name{margin-top:6px;font-size:10px;font-weight:600;color:var(--navy)}
  .social{display:flex;align-items:center;gap:8px;font-size:6.6px;color:#fff;margin-bottom:9px}
  .social__box{width:12px;height:12px;border:1.3px solid #fff;border-radius:2px}
  .tagline{font-style:italic}
  .strong-line{font-weight:700;font-size:8px;color:var(--navy)}
</style>
</head>
<body>

<!-- ===== Inside spread ===== -->
<section class="spread spread--inside">
  <svg class="wave" style="left:0;top:0" width="800" height="45" viewBox="0 0 800 45">
    <path d="M0 40 C120 10 260 12 420 0 L0 0Z" fill="var(--sea)"/>
    <path d="M0 28 C140 6 300 6 460 0 L0 0Z" fill="var(--sea-light)"/>
    <path d="M0 14 C120 2 240 2 360 0 L0 0Z" fill="var(--sea-pale)"/>
  </svg>

  <div class="headline-bar">Our boats, Salwa and Coral 1, fully adapted to the needs of divers and snorkelers.</div>

  <div class="block" style="left:20px;top:58px;width:238px">
    <h3>Daily boat</h3>
    <p>Enjoy a day at sea, diving and snorkeling in Marsa Mubarak. If you're lucky, you'll see the dugong and the big turtles. Snorkel in Meroka with the dolphins and along the islands of Hamata.</p>
  </div>
  <div class="block" style="left:20px;top:132px;width:238px">
    <h3>Liveaboards</h3>
    <p>Experience a fantastic week on the Red Sea and explore some of the most stunning and colourful dive sites in the world. Find your favourite sites on our North Tour, South Tour or Deep South.</p>
  </div>

  <div class="photo" role="img" aria-label="Photo of the yacht Salwa at sea" style="left:281px;top:56px;width:239px;height:141px;background:linear-gradient(180deg,#bcd9ee 0%,#e7eef3 45%,#1f4f86 70%,#123a6b 100%)"></div>
  <div class="photo" role="img" aria-label="Photo of the white yacht Coral 1 at anchor" style="left:541px;top:56px;width:239px;height:141px;background:linear-gradient(180deg,#2f8ad8 0%,#7fbbe8 40%,#f2f4f6 60%,#1e5fa8 100%)"></div>

  <div class="abs navy" style="left:0;top:200px;width:800px;height:163px"></div>
  <div class="photo" role="img" aria-label="Photo of two divers underwater giving the okay sign" style="left:17px;top:211px;width:241px;height:142px;background:linear-gradient(180deg,#1b8fd8,#0d5aa6 70%,#0a3f80)"></div>
  <div class="photo" role="img" aria-label="Photo of the boat saloon with blue sofas" style="left:281px;top:211px;width:239px;height:142px;background:linear-gradient(180deg,#6b5a3a,#2b3f66 45%,#8a6a44 100%)"></div>
  <div class="photo" role="img" aria-label="Photo of the boat dining room" style="left:541px;top:211px;width:239px;height:142px;background:linear-gradient(180deg,#5a3a2a,#7a4c34 50%,#3a2a22 100%)"></div>

  <div class="block" style="left:20px;top:378px;width:238px">
    <h3>Full charter</h3>
    <p>Are you a larger group of divers or a dive club and want to be among yourselves on the boat? Then a full charter may be the best option.<br>Let us know your ideas, conditions, wishes and diving experience. We will plan an individual full charter considering your details and the conditions at hand.</p>
  </div>
  <div class="block" style="left:20px;top:486px;width:238px">
    <h3>Diving courses</h3>
    <p>Learn to dive with our passionate instructors. As a partner of BEMO and QRX we train you in all levels from Scuba Diver to Dive Master. The courses can also be done during a liveaboard, depending on the conditions.</p>
  </div>

  <div class="block" style="left:281px;top:378px;width:240px">
    <h3>Salwa</h3>
    <p>MY Salwa was built in 2019.<br>With a length of 30 metres and a beam of 8 metres, the steel-constructed boat comfortably accommodates 18 guests. 5 twin bed cabins and 2 double bed cabins are located on the lower deck and 2 single bed cabins on the upper deck.</p>
  </div>
  <div class="block" style="left:543px;top:378px;width:240px">
    <h3>Coral 1</h3>
    <p>MY Coral 1 was built in 2021.<br>With a length of 32 metres and a beam of 8 metres, the steel-constructed boat comfortably accommodates 24 guests. 8 cabins with twin beds are located on the lower deck and 4 cabins on the upper deck.</p>
  </div>

  <div class="abs navy on-navy" style="left:270px;top:463px;width:530px;height:107px;padding:12px 20px 0 10px">
    <p>The restaurant on the main deck serves 3 buffets a day, and the spacious dive deck is where you get ready for adventure.<br>On the top deck, there is plenty of shaded seating and a bar for socialising and relaxing.<br>On the top deck, comfortable loungers await, ideal for enjoying the sun or watching the stars.</p>
  </div>
  <svg class="wave" style="left:480px;top:470px" width="320" height="100" viewBox="0 0 320 100">
    <path d="M320 0 C260 60 160 90 0 100 L320 100Z" fill="var(--sea)"/>
    <path d="M320 30 C270 70 200 92 100 100 L320 100Z" fill="var(--sea-light)"/>
    <path d="M320 60 C290 80 250 94 200 100 L320 100Z" fill="var(--sea-pale)"/>
  </svg>
</section>

<!-- ===== Outside spread ===== -->
<section class="spread spread--outside">
  <svg class="wave" style="left:0;top:0" width="267" height="60" viewBox="0 0 267 60">
    <path d="M0 58 C60 20 150 8 267 4 L267 0 L0 0Z" fill="var(--sea)"/>
    <path d="M0 40 C70 12 160 4 267 2 L267 0 L0 0Z" fill="var(--sea-light)"/>
    <path d="M0 20 C60 6 140 2 267 0 L0 0Z" fill="var(--sea-pale)"/>
  </svg>

  <div class="block" style="left:18px;top:32px;width:236px">
    <h3>Full charter</h3>
    <p>Spend a week on a full charter at Meroka and/or Fury Shoals. Snorkel, dive, enjoy the time. Our boats offer plenty of space for rest, meditation or yoga. The region is perfect for the whole family. We look forward to seeing you and having an unforgettable time</p>
  </div>
  <div class="block" style="left:18px;top:145px;width:236px">
    <h3>Mini Safari</h3>
    <p>Two nights at sea, ideal for snorkeling and diving at various locations in Fury Shoals.</p>
  </div>
  <div class="block" style="left:18px;top:220px;width:236px">
    <h3>Overnight</h3>
    <p>Take a short break. Enjoy the sun, the stars and the sea. Experience the beauty of Meroka and spend a night on the boat. Explore the colourful reefs during your dives, or swim and snorkel with the dolphins and let them touch your soul.</p>
  </div>
  <div class="block" style="left:18px;top:312px;width:236px">
    <h3>Daily boat</h3>
    <p>Sail to Meroka for a day. Swim and snorkel with the dolphins, enjoy a delicious lunch and go snorkeling again.</p>
  </div>
  <div class="block strong-line" style="left:0;top:368px;width:267px;text-align:center">Tours start and end at Hamata harbour.</div>
  <div class="photo" role="img" aria-label="Photo of the dive centre building on the beach" style="left:0;top:392px;width:267px;height:178px;background:linear-gradient(180deg,#2e8fe0 0%,#8cc6f0 35%,#2a5f9a 60%,#b9a98c 100%)"></div>

  <div class="photo" role="img" aria-label="Photo of a pod of dolphins swimming underwater" style="left:267px;top:0;width:533px;height:222px;background:linear-gradient(180deg,#2fa8ea 0%,#1a86d6 50%,#0d5cb0 100%)"></div>

  <div class="abs navy on-navy" style="left:267px;top:222px;width:262px;height:348px;padding:8px 12px 0 12px">
    <h3 style="margin-bottom:4px">Diving Centre</h3>
    <p>We are based at the Hotel Belvano, south of El Quseir. From here we depart daily for diving and snorkeling along the house reef, from the beach to the surrounding reefs and our daily boats from Port Ghalib and Hamata. Our team will accompany you professionally during your first breaths under water, train you according to QRX and BEMO standards or guide you safely along the dive sites.<br>We offer attractive packages with hotel and diving.</p>
  </div>
  <div class="photo" role="img" aria-label="Aerial photo of the hotel resort with pools by the sea" style="left:272px;top:350px;width:252px;height:131px;background:linear-gradient(180deg,#5b8fc6 0%,#9bb8d2 15%,#8a7a5e 45%,#3fa5c9 65%,#a89272 100%)"></div>
  <div class="abs on-navy" style="left:273px;top:492px;width:130px">
    <p>Tarek +20 100 000 1234<br>Petra +41 79 000 11 22</p>
    <p style="margin-top:10px;font-size:7px;font-weight:600">www.veloradivingsafari.example</p>
    <p>info@veloradivingsafari.example</p>
  </div>
  <div class="abs" style="left:407px;top:490px">
    <div class="social"><span class="social__box"></span>velora_diving_safari</div>
    <div class="social"><span class="social__box"></span>veloradiving.20</div>
    <div class="social"><span class="social__box"></span>Velora Diving Safari</div>
  </div>

  <div class="brand" style="left:600px;top:232px">
    <span class="brand__mark"></span>
    <span class="brand__name">Velora Diving Safari</span>
  </div>
  <div class="block" style="left:537px;top:336px;width:260px">
    <h3 style="font-size:9.5px;margin-bottom:12px">Velora Diving Safari - Discover the Red Sea</h3>
  </div>
  <div class="block" style="left:545px;top:365px;width:240px">
    <p>We show you our great, diverse home with the most beautiful dive sites. Whether you are an experienced diver or just starting your diving adventure, discover with us the beauty of the underwater world with its varied corals and fish.<br>Escape the daily routine with us.</p>
    <p style="margin-top:9px">We look forward to welcoming you!</p>
    <p style="margin-top:9px">Team Velora Diving Safari<br>Tarek &amp; Petra<br><span class="tagline">…and into the ocean we go, to lose our mind and find our soul</span></p>
  </div>
  <svg class="wave" style="left:529px;top:440px" width="271" height="130" viewBox="0 0 271 130">
    <path d="M271 0 C250 70 140 110 0 120 L0 130 L271 130Z" fill="var(--sea)"/>
    <path d="M271 40 C240 90 150 118 30 130 L271 130Z" fill="var(--sea-light)"/>
    <path d="M271 80 C240 110 180 124 120 130 L271 130Z" fill="var(--sea-pale)"/>
  </svg>
</section>

</body>
</html>
```